Bold Flyer Needed for Bold Little Gym

We need a 1 page flyer created for our small boutique fitness facility, CorVanto, which highlights a new service we are offering.
We are now offering Red Light Therapy (RLT) to our members and I need a full color, 1 page flyer created that captures the eye of our members while highlighting the benefits and clearly stating the prices at the bottom of the page.
Flyer will be printed out on a standard 8.5" x 11" sheet of paper and should be laid out in a way that is easy to read. Landscape or Portrait layouts are both expectable.
We are using Silverline Glow Therapy Lights LumaCore 700 Lamps as found here http://lnk.example/7QWRT5Z
I have attached the text that should be included and our logo for branding of the flyer.
Thank you!

```html
<!DOCTYPE html>
<html lang="en">
<head>
<meta charset="utf-8">
<title>CorVanto Red Light Therapy Flyer</title>
<link href="https://fonts.googleapis.com/css2?family=Poppins:wght@400;500;600;700;800;900&display=swap" rel="stylesheet">
<style>
:root{
  --ink:#0d0d0d;
  --yellow:#f6cf0c;
  --white:#ffffff;
  --grey:#d6d7d9;
  --stage:#e4e5e7;
  --red:#d8261c;
}
*{box-sizing:border-box;margin:0;padding:0}
html,body{width:1200px;height:1117px;overflow:hidden;background:var(--stage);font-family:'Poppins',sans-serif;color:var(--ink)}
.flyer{position:absolute;left:192px;top:30px;width:816px;height:1056px;background:var(--white);overflow:hidden;box-shadow:0 6px 24px rgba(0,0,0,.18)}
.header{position:absolute;left:0;top:0;width:816px;height:340px;
  background:radial-gradient(ellipse at 78% 35%,#4a4410 0%,#1c1a08 40%,var(--ink) 70%);
  clip-path:polygon(0 0,100% 0,100% 100%,0 78%)}
.hero-photo{position:absolute;left:0;top:0;width:250px;height:175px;
  background:radial-gradient(ellipse at 45% 45%,#ff3a22 0%,var(--red) 40%,#3a0604 80%,var(--ink) 100%)}
.brand{position:absolute;left:330px;top:30px;width:440px;text-align:center}
.brand-name{font-weight:900;font-size:84px;line-height:1;color:var(--white);letter-spacing:-1px}
.brand-tag{margin-top:8px;font-weight:700;font-size:13px;letter-spacing:4px;color:var(--yellow)}
.headline{position:absolute;left:250px;top:168px;width:540px;text-align:center;color:var(--white);font-weight:800;font-size:28px;line-height:1.15}
.headline em{font-style:normal;color:var(--yellow)}
.intro-band{position:absolute;left:120px;top:262px;width:660px;height:42px;background:var(--yellow);
  clip-path:polygon(2% 0,100% 0,96% 100%,0 100%);display:flex;align-items:center;justify-content:center;
  font-weight:700;font-size:21px}
.transform{position:absolute;left:0;top:346px;width:816px;text-align:center;font-weight:700;font-size:23px;line-height:1.3}
.benefits{position:absolute;left:40px;top:398px;width:370px}
.label-dark{display:inline-block;background:var(--ink);color:var(--white);font-weight:700;font-size:18px;padding:6px 22px;margin-left:-10px;position:relative;z-index:1}
.benefit-box{border:3px solid var(--yellow);margin-top:-8px;padding:20px 16px 10px 20px}
.point{position:relative;padding-left:16px;margin-bottom:8px}
.point::before{content:"";position:absolute;left:0;top:7px;width:6px;height:6px;border-radius:50%;background:var(--ink)}
.point h3{font-weight:700;font-size:15px;line-height:1.25}
.point p{font-size:13px;line-height:1.3}
.why{position:absolute;left:440px;top:400px;width:340px}
.why .point{margin-bottom:6px}
.label-grey{background:var(--grey);font-weight:700;font-size:18px;text-align:center;padding:5px 0;margin-bottom:10px}
.offer{position:absolute;left:440px;top:684px;width:340px;text-align:center}
.offer-band{background:var(--yellow);font-weight:700;font-size:20px;padding:4px 0;margin-bottom:8px}
.offer-price{font-weight:600;font-size:16px;line-height:1.25}
.offer-price strong{font-size:24px;font-weight:800}
.rule{height:2px;background:var(--yellow);margin:6px 0}
.limited{font-weight:800;font-size:21px;line-height:1.2}
.offer-note{font-size:13px;line-height:1.35}
.contact{position:absolute;left:40px;top:846px;width:270px}
.contact h2{font-weight:800;font-size:30px;line-height:1.1;padding-bottom:6px;border-bottom:2px solid var(--yellow)}
.contact h2 span{color:var(--yellow)}
.contact .lead{font-size:13px;margin-top:6px}
.phone{display:flex;align-items:center;gap:6px;font-weight:800;font-size:28px;line-height:1.2;margin:2px 0}
.phone .area{color:var(--yellow)}
.contact .tail{font-size:13px}
.signoff{margin-top:8px;font-weight:700;font-size:12px;line-height:1.3}
.prices{position:absolute;left:300px;top:880px;width:516px;height:154px;
  background:radial-gradient(ellipse at 85% 70%,#3d3910 0%,var(--ink) 60%);
  clip-path:polygon(22% 0,100% 0,100% 100%,0 100%);color:var(--white)}
.price-table{position:absolute;left:110px;top:16px;width:390px;font-size:14px;font-weight:700}
.price-head{display:grid;grid-template-columns:130px 126px 122px;gap:6px;margin-bottom:6px}
.price-head span{border:2px solid var(--white);color:var(--yellow);text-align:center;padding:1px 0;font-size:12px;white-space:nowrap}
.price-row{display:grid;grid-template-columns:130px 126px 122px;gap:6px;line-height:22px;white-space:nowrap}
.price-row span:nth-child(2),.price-row span:nth-child(3){text-align:right;padding-right:10px}
.footer-strip{position:absolute;left:0;bottom:0;width:816px;height:22px;background:var(--yellow)}
</style>
</head>
<body>
<main class="flyer">
  <section class="header">
    <div class="hero-photo" role="img" aria-label="Photo of a person in protective glasses bathed in red therapy light"></div>
    <div class="brand">
      <div class="brand-name">CorVanto</div>
      <div class="brand-tag">PERSONAL GROUP TRAINING</div>
    </div>
    <h1 class="headline">Unlock Your Potential with Red Light Therapy at <em>CorVanto!</em></h1>
  </section>
  <div class="intro-band">Introducing Our New Red Light Therapy Room!</div>

  <h2 class="transform">Transform Your Wellness Routine with the Power of Light!</h2>

  <section class="benefits">
    <div class="label-dark">Benefits of Red Light Therapy</div>
    <div class="benefit-box">
      <div class="point"><h3>Boosts Energy Levels</h3><p>Feel revitalized and more energetic after each session.</p></div>
      <div class="point"><h3>Enhances Muscle Recovery</h3><p>Speed up recovery times post-workout and reduce soreness.</p></div>
      <div class="point"><h3>Improves Skin Health</h3><p>Reduce wrinkles, blemishes, and promote a youthful glow</p></div>
      <div class="point"><h3>Supports Joint Health</h3><p>Alleviate pain and inflammation, making movement easier.</p></div>
      <div class="point"><h3>Promotes Better Sleep</h3><p>Improve your sleep patterns and overall restfulness.</p></div>
      <div class="point"><h3>Increases Circulation</h3><p>Enhance blood flow for better nutrient delivery to muscles.</p></div>
    </div>
  </section>

  <section class="why">
    <div class="label-grey">Why Choose CorVanto?</div>
    <div class="point"><h3>State-of-the-Art Equipment</h3><p>Experience the power of eight Silverline Glow LumaCore 700 panels—some of the best on the market!</p></div>
    <div class="point"><h3>Expert Guidance</h3><p>Our trained staff will guide you through each session to ensure you get the most out of your therapy.</p></div>
    <div class="point"><h3>Community Focused</h3><p>Join a supportive community that prioritizes health and wellness.</p></div>
  </section>

  <section class="offer">
    <div class="offer-band">Special Introductory Offer!</div>
    <p class="offer-price">Try Your First Session for Just <strong>$25!</strong><br>(Regularly $55)</p>
    <div class="rule"></div>
    <p class="limited">Limited Time Only!</p>
    <div class="rule"></div>
    <p class="offer-note">Book your session today and discover how Red Light Therapy can elevate your fitness journey.</p>
  </section>

  <section class="contact">
    <h2>Ready to <span>Shine?</span></h2>
    <p class="lead">Visit our front desk or call us at</p>
    <p class="phone">
      <svg width="20" height="24" viewBox="0 0 22 26" aria-hidden="true"><path d="M6 2 L10 8 L7 11 Q9 16 13 19 L16 16 L21 20 L18 24 Q10 24 4 14 Q1 8 3 4 Z" fill="var(--yellow)"/></svg>
      <span class="area">(555)</span> 014-2290
    </p>
    <p class="tail">to schedule your appointment.</p>
    <p class="signoff">CorVanto Fitness Facility,<br>Your Wellness, Our Commitment!</p>
  </section>

  <section class="prices">
    <div class="price-table">
      <div class="price-head"><span>PRICES</span><span>CorVanto Member</span><span>Non-Member</span></div>
      <div class="price-row"><span>Single Session</span><span>$35</span><span>$55</span></div>
      <div class="price-row"><span>3 - Pack</span><span>$102</span><span>$159</span></div>
      <div class="price-row"><span>5 - Pack</span><span>$167</span><span>$259</span></div>
      <div class="price-row"><span>10 - Pack</span><span>$316</span><span>$491</span></div>
    </div>
  </section>
  <div class="footer-strip"></div>
</main>
</body>
</html>
```